Steadfast Corner Vending Needs a Promotional Flyer

Design a one page, one sided 8 1/2" x 11" flyer that can be handed out to potential customers. Please keep printing efficiencies in mind. See attached old flyers and company website (steadfastcornervend.example) for reference of services. I have also attached our current logo.

```html
<!DOCTYPE html>
<html lang="en">
<head>
<meta charset="utf-8">
<title>Steadfast Corner Vending – Flyer</title>
<link href="https://fonts.googleapis.com/css2?family=Poppins:wght@400;500;600;700;800&display=swap" rel="stylesheet">
<style>
:root{
  --navy:#13293d;
  --blue:#1b93cf;
  --blue-label:#1e9ad6;
  --white:#ffffff;
  --page-bg:#e9ebee;
  --text:#13293d;
}
*{margin:0;padding:0;box-sizing:border-box}
html,body{width:1200px;height:2415px;overflow:hidden;background:var(--page-bg);font-family:'Poppins',sans-serif;color:var(--text)}
.flyer{position:absolute;left:40px;top:483px;width:1120px;height:1449px;background:var(--white);overflow:hidden;box-shadow:0 6px 24px rgba(0,0,0,.18)}
.abs{position:absolute}
.hero-blue{left:660px;top:0;width:460px;height:575px;background:var(--blue)}
.hero-navy{left:925px;top:16px;width:195px;height:545px;background:var(--navy)}
.brand{left:104px;top:84px;width:370px;text-align:center;font-weight:700;font-size:30px;line-height:1.1;color:var(--navy);letter-spacing:.5px;white-space:nowrap}
.brand-mark{display:block;width:38px;height:38px;background:var(--blue);margin:0 auto 12px}
.headline{left:94px;top:252px;font-weight:800;text-transform:uppercase;line-height:1}
.headline .small{display:block;font-size:60px;color:var(--navy);margin-bottom:6px}
.headline .big{display:block;font-size:100px;color:var(--blue);letter-spacing:-1px;line-height:.86}
.badge{left:743px;top:44px;width:124px;height:124px;border-radius:50%;background:var(--navy);display:flex;align-items:center;justify-content:center}
.badge-inner{width:98px;height:98px;border-radius:50%;background:var(--white);display:flex;flex-direction:column;align-items:center;justify-content:center;line-height:1}
.badge-inner .num{font-size:32px;font-weight:800;color:var(--navy)}
.badge-inner .yr{font-size:14px;font-weight:700;color:var(--blue)}
.badge-inner .exp{font-size:7px;font-weight:600;color:var(--navy);letter-spacing:.5px;margin-top:2px}
.machines{left:602px;top:175px;width:466px;height:394px;background:linear-gradient(90deg,#2a2d33 0%,#4a4f58 44%,#d8321e 52%,#e84a24 100%)}
.why{left:55px;top:575px;width:991px;height:239px;background:var(--navy);color:var(--white)}
.why h2{position:absolute;left:39px;top:22px;font-size:28px;font-weight:400}
.why h2 b{color:var(--blue);font-weight:700}
.why-item{position:absolute;display:flex;gap:14px;font-size:15px;line-height:1.2;font-weight:400}
.why-item svg{flex:none;width:32px;height:32px}
.section-title{left:94px;top:848px;font-size:34px;font-weight:800;color:var(--navy)}
.label{background:var(--blue-label);color:var(--white);font-weight:700;font-size:23px;line-height:1;padding:3px 9px;text-transform:uppercase}
.photo{border:2px solid var(--navy)}
.list{list-style:none;font-size:14px;font-weight:600;line-height:1.2;color:var(--navy)}
.list li{position:relative;padding-left:16px}
.list li::before{content:"";position:absolute;left:2px;top:6px;width:7px;height:7px;border-radius:50%;background:var(--blue)}
.list .ticks li{padding-left:0}
.list .ticks li::before{content:"✓ ";position:static;width:auto;height:auto;background:none;font-size:11px}
.ticks{display:grid;font-size:14px;font-weight:400;line-height:1.2;list-style:none;color:var(--navy);margin:2px 0 4px 0;column-gap:14px}
.footer-navy{left:0;top:1342px;width:460px;height:107px;background:var(--navy);clip-path:polygon(0 0,420px 0,460px 107px,0 107px)}
.footer-line{left:0;top:1441px;width:1120px;height:8px;background:var(--blue)}
.call{left:102px;top:1350px;color:var(--white);font-weight:600;line-height:1}
.call .lbl{font-size:23px;display:block;margin-bottom:10px}
.call .num{font-size:36px;display:flex;align-items:center;gap:10px}
.contact{top:1378px;display:flex;gap:10px;font-size:17px;line-height:1.2;color:var(--navy)}
</style>
</head>
<body>
<main class="flyer">
  <div class="abs hero-blue"></div>
  <div class="abs hero-navy"></div>

  <div class="abs brand"><span class="brand-mark"></span>STEADFAST CORNER<br>VENDING</div>

  <h1 class="abs headline">
    <span class="small">Welcome</span>
    <span class="small">to Steadfast</span>
    <span class="big">Corner</span>
    <span class="big">Vending</span>
  </h1>

  <div class="abs machines" role="img" aria-label="Photo of a snack vending machine beside a red cold-drink vending machine"></div>

  <div class="abs badge"><div class="badge-inner"><span class="num">35</span><span class="yr">YEAR</span><span class="exp">EXPERIENCE</span></div></div>

  <section class="abs why">
    <h2>Why Choose Our <b>Vending Machine Services?</b></h2>
    <div class="why-item" style="left:39px;top:78px;width:320px"><svg viewBox="0 0 32 32"><circle cx="16" cy="16" r="14" fill="none" stroke="#1b93cf" stroke-width="2.5"/><path d="M16 9v7l5 3" stroke="#fff" stroke-width="2.5" fill="none"/></svg><span>Our warehouse is just minutes away so we can get there quickly if a problem should arise.</span></div>
    <div class="why-item" style="left:39px;top:148px;width:320px"><svg viewBox="0 0 32 32"><circle cx="16" cy="16" r="14" fill="none" stroke="#1b93cf" stroke-width="2.5"/><rect x="11" y="9" width="10" height="14" fill="none" stroke="#fff" stroke-width="2"/></svg><span>We are a small company<br>that is BIG on service.</span></div>
    <div class="why-item" style="left:39px;top:198px;width:320px"><svg viewBox="0 0 32 32"><circle cx="16" cy="16" r="14" fill="none" stroke="#1b93cf" stroke-width="2.5"/><circle cx="16" cy="13" r="3.5" fill="#fff"/><path d="M9 23c1-4 13-4 14 0" fill="#fff"/></svg><span>Customer Service is our priority.</span></div>
    <div class="why-item" style="left:378px;top:80px;width:280px"><svg viewBox="0 0 32 32"><circle cx="16" cy="16" r="14" fill="none" stroke="#1b93cf" stroke-width="2.5"/><path d="M10 16l4 4 8-8" stroke="#fff" stroke-width="2.5" fill="none"/></svg><span>We are Owner-Operators so we truly CARE about our customers.</span></div>
    <div class="why-item" style="left:378px;top:150px;width:280px"><svg viewBox="0 0 32 32"><circle cx="16" cy="16" r="14" fill="none" stroke="#1b93cf" stroke-width="2.5"/><path d="M16 8a5 5 0 0 1 3 9v5h-6v-5a5 5 0 0 1 3-9z" fill="#fff"/></svg><span>We are also trained to fix many problems on the spot.</span></div>
    <div class="why-item" style="left:673px;top:80px;width:310px"><svg viewBox="0 0 32 32"><circle cx="16" cy="16" r="14" fill="none" stroke="#1b93cf" stroke-width="2.5"/><path d="M10 13h12M10 17h12M10 21h8" stroke="#fff" stroke-width="2"/></svg><span>We will supply machines<br>to your facility.</span></div>
    <div class="why-item" style="left:673px;top:132px;width:310px"><svg viewBox="0 0 32 32"><circle cx="16" cy="16" r="14" fill="none" stroke="#1b93cf" stroke-width="2.5"/><circle cx="11" cy="14" r="2.5" fill="#fff"/><circle cx="21" cy="14" r="2.5" fill="#fff"/><circle cx="16" cy="12" r="2.5" fill="#fff"/><path d="M8 22c1-4 15-4 16 0" fill="#fff"/></svg><span>Your employees can choose what types of snacks and drinks they would like to see in the machines.</span></div>
  </section>

  <h2 class="abs section-title">STEADFAST SUPERIOR SERVICE</h2>

  <!-- Vending machine services -->
  <div class="abs label" style="left:94px;top:900px;width:248px;height:56px;font-size:22px;padding-top:6px">Vending Machine Services</div>
  <div class="abs photo" style="left:354px;top:900px;width:173px;height:128px;background:linear-gradient(180deg,#f4f6f8,#8c96a4 50%,#2d4d8f)" role="img" aria-label="Photo of a glass-front snack and drink vending machine"></div>
  <ul class="abs list" style="left:94px;top:966px;width:255px">
    <li>Discover Reliability,</li><li>Variety At Zero Cost to You</li><li>Convenience</li><li>Quality</li>
  </ul>

  <!-- Coffee -->
  <div class="abs label" style="left:94px;top:1057px;width:234px">Coffee Service</div>
  <div class="abs photo" style="left:354px;top:1057px;width:173px;height:131px;border:none;background:radial-gradient(circle at 60% 55%,#f3f1ee 0 28%,#6b3e22 45%,#3a2012 100%)" role="img" aria-label="Photo of a white cup of coffee surrounded by coffee beans"></div>
  <ul class="abs list" style="left:94px;top:1088px;width:440px">
    <li>Reliability</li><li>Our Coffee Selection
      <ul class="ticks" style="grid-template-columns:105px 105px">
        <li>Harborline</li><li>Ridgeback</li><li>Morning Mill</li><li>Copperpot</li><li>Pale Summit</li><li>Hearthstone</li><li>Brightwater</li>
      </ul></li>
    <li>Tea and other Tasty Hot Beverages</li><li>Coffee Accessories
      <ul class="ticks" style="grid-template-columns:100px 100px 150px">
        <li>Coffee Pots</li><li>Sleeves</li><li>Sweetdrop</li><li>Filters</li><li>Napkins</li><li>Liquid Creamers</li><li>Cups</li><li>Sugar</li><li>flavored and regular</li><li>Stirrers</li><li>Lite-n-Fine</li>
      </ul></li>
  </ul>

  <!-- Pantry -->
  <div class="abs label" style="left:584px;top:900px;width:246px">Pantry Service</div>
  <div class="abs photo" style="left:851px;top:900px;width:174px;height:129px;background:linear-gradient(90deg,#5a3a26,#9a6a44 40%,#c9a27a 65%,#3b3f48)" role="img" aria-label="Photo of an office pantry with wooden snack shelves and a drink cooler"></div>
  <ul class="abs list" style="left:584px;top:935px;width:262px">
    <li>A Snack Time Oasis in Your Workspace</li><li>Tailored to Your Tastes</li><li>Healthy Choices, Happy Teams</li><li>Seamless Restocking and Management</li><li>Flexible and Hassle-Free</li><li>Enhancing Workplace Culture</li>
  </ul>

  <!-- Micro-market -->
  <div class="abs label" style="left:584px;top:1108px;width:246px">Micro-Market</div>
  <div class="abs photo" style="left:851px;top:1108px;width:174px;height:129px;background:linear-gradient(90deg,#b07a3a,#d23a2a 35%,#e8b23a 60%,#2b5aa0)" role="img" aria-label="Photo of micro-market shelves stocked with colorful snacks"></div>
  <ul class="abs list" style="left:584px;top:1142px;width:262px">
    <li>Experience Unmatched Convenience</li><li>Tailored to Your Taste</li><li>Seamless and Secure Transactions</li><li>Freshness Guaranteed</li><li>Smart Inventory Management</li><li>Promoting Workplace Wellbeing</li>
  </ul>

  <!-- Footer -->
  <div class="abs footer-line"></div>
  <svg class="abs" style="left:0;top:1342px" width="480" height="107" viewBox="0 0 480 107"><polygon points="462,0 472,0 480,107 470,107" fill="#1b93cf"/></svg>
  <div class="abs footer-navy"></div>
  <div class="abs call"><span class="lbl">CALL US AT</span><span class="num"><svg width="24" height="24" viewBox="0 0 24 24"><path d="M6 2l4 4-2 3c1 3 4 6 7 7l3-2 4 4-3 4C11 22 2 13 2 5z" fill="#1b93cf"/></svg>555-010-4823</span></div>
  <div class="abs contact" style="left:490px"><svg width="20" height="24" viewBox="0 0 20 24"><path d="M10 1a8 8 0 0 1 8 8c0 6-8 14-8 14S2 15 2 9a8 8 0 0 1 8-8z" fill="none" stroke="#1b93cf" stroke-width="2.2"/><circle cx="10" cy="9" r="3" fill="#1b93cf"/></svg><span>1480 Lantern Ave, Unit 210,<br>Maple Ridge, IL 60000</span></div>
  <div class="abs contact" style="left:778px"><svg width="22" height="22" viewBox="0 0 22 22"><circle cx="11" cy="11" r="9" fill="none" stroke="#1b93cf" stroke-width="2"/><path d="M2 11h18M11 2c-4 5-4 13 0 18M11 2c4 5 4 13 0 18" fill="none" stroke="#1b93cf" stroke-width="1.6"/></svg><span>steadfastcornervend.example</span></div>
</main>
</body>
</html>
```